Walk Beside The River

Business Card design

Target Market(s)

People who require support in the commnity

Industry/Entity Type

Mental Health Support

Contact Information for Business Card

Mental Health Support Rosalind Tavener walkbesidetheriver@mailcove.com.au 0481 637 092 PO Box 926 Kestrel Bay VIC 3991

Colors
6B429C
8869AF
B7A5CE
E3DAEB
F3F0F8

Requirements
Must have
• Logo & details listed above
Should not have
• No red or orange

```html
<!DOCTYPE html>
<html lang="en">
<head>
<meta charset="utf-8">
<title>Walk Beside The River – Business Card</title>
<link rel="stylesheet" href="https://fonts.googleapis.com/css2?family=Lato:wght@400;700;900&display=swap">
<style>
  :root {
    --stage: #2b2b2b;
    --card-back: #6b429c;
    --violet-deep: #8a2be0;
    --violet-mid: #b23ee8;
    --violet-light: #d452ec;
    --badge: #6b429c;
    --accent: #f2ea1c;
    --ink: #ffffff;
    --radius: 18px;
  }
  * { box-sizing: border-box; margin: 0; padding: 0; }
  html, body {
    width: 1200px; height: 875px; overflow: hidden;
    background: var(--stage);
    font-family: "Lato", sans-serif;
  }
  .canvas {
    width: 1200px; height: 875px;
    display: flex; align-items: center; justify-content: center; gap: 40px;
  }
  .card {
    width: 540px; height: 309px;
    border-radius: var(--radius);
    position: relative; overflow: hidden;
  }

  /* Front */
  .card-front { background: var(--violet-mid); }
  .front-backdrop {
    position: absolute; inset: 0;
    background:
      radial-gradient(ellipse at 70% 25%, var(--violet-light) 0%, transparent 55%),
      radial-gradient(ellipse at 20% 75%, var(--violet-deep) 0%, transparent 60%),
      linear-gradient(135deg, var(--violet-light), var(--violet-mid) 50%, var(--violet-deep));
  }
  .front-badge {
    position: absolute; left: 50%; top: 50%;
    width: 290px; height: 290px; margin: -145px 0 0 -145px;
    border-radius: 50%;
    background: var(--badge);
    display: flex; align-items: center; justify-content: center;
    gap: 12px; padding: 0 30px;
  }
  .brand-dot {
    width: 14px; height: 14px; border-radius: 50%;
    background: var(--accent); flex: none;
  }
  .brand-name {
    color: var(--ink); font-weight: 900;
    font-size: 22px; line-height: 1.2; letter-spacing: 0.12em;
    text-transform: uppercase; text-align: center;
  }

  /* Back */
  .card-back {
    background: var(--card-back);
    display: flex; align-items: center;
    padding: 0 30px 0 40px; gap: 26px;
  }
  .back-brand {
    width: 170px; flex: none;
    color: var(--accent); font-weight: 900;
    font-size: 20px; line-height: 1.25; letter-spacing: 0.06em;
    text-transform: uppercase;
  }
  .details { color: var(--ink); min-width: 0; }
  .person-name {
    font-weight: 900; font-size: 25px; line-height: 1.05;
    text-transform: uppercase; letter-spacing: 0.01em;
    white-space: nowrap;
  }
  .role {
    color: var(--accent); font-weight: 400; font-size: 16px;
    margin: 3px 0 12px;
  }
  .contact-list { list-style: none; }
  .contact-item {
    display: flex; align-items: center; gap: 8px;
    font-size: 11.5px; line-height: 1.75; white-space: nowrap;
  }
  .contact-item.phone { font-size: 18px; font-weight: 700; }
  .contact-icon { width: 12px; height: 12px; flex: none; fill: var(--accent); }
  .contact-icon.outline { fill: none; stroke: var(--accent); stroke-width: 2; }
</style>
</head>
<body>
<main class="canvas">

  <section class="card card-front" aria-label="Card front">
    <div class="front-backdrop" role="img" aria-label="Soft violet starry nebula background with fine wave lines"></div>
    <div class="front-badge">
      <span class="brand-dot"></span>
      <span class="brand-name">Walk Beside The River</span>
    </div>
  </section>

  <section class="card card-back" aria-label="Card back">
    <div class="back-brand">Walk Beside The River</div>
    <div class="details">
      <h1 class="person-name">Rosalind Tavener</h1>
      <p class="role">Mental Health Support</p>
      <ul class="contact-list">
        <li class="contact-item phone">
          <svg class="contact-icon" viewBox="0 0 24 24" aria-hidden="true"><path d="M6.6 10.8a15 15 0 0 0 6.6 6.6l2.2-2.2a1 1 0 0 1 1-.25 11.4 11.4 0 0 0 3.6.57 1 1 0 0 1 1 1V20a1 1 0 0 1-1 1A17 17 0 0 1 3 4a1 1 0 0 1 1-1h3.5a1 1 0 0 1 1 1c0 1.25.2 2.45.57 3.57a1 1 0 0 1-.25 1z"/></svg>
          0481 637 092
        </li>
        <li class="contact-item">
          <svg class="contact-icon outline" viewBox="0 0 24 24" aria-hidden="true"><path d="M2 5h20v14H2z M3 6l9 7 9-7"/></svg>
          walkbesidetheriver@mailcove.com.au
        </li>
        <li class="contact-item">
          <svg class="contact-icon" viewBox="0 0 24 24" aria-hidden="true"><path d="M12 2a7 7 0 0 0-7 7c0 5 7 13 7 13s7-8 7-13a7 7 0 0 0-7-7zm0 9.5A2.5 2.5 0 1 1 12 6.5a2.5 2.5 0 0 1 0 5z"/></svg>
          PO Box 926 Kestrel Bay VIC 3991
        </li>
      </ul>
    </div>
  </section>

</main>
</body>
</html>
```